Logistics Website Design

See website https://tqfreightglobal.com for theme and color details. Need the site to be re-done and reflect some of the designs shown in this list here: https://pixelvane.com/tags/logistics-company-website

Target Market(s)

Logistics & Transportation

Industry/Entity Type

Logistics and Supply Chain

Coding

Number of Pages Required

5+ page

Requirements
Must have
• Colors must match theme of logo. Looking for a sleek, interactive design.

```html
<!DOCTYPE html>
<html lang="en">
<head>
<meta charset="utf-8">
<title>Corvane Freight — Contact Us</title>
<link href="https://fonts.googleapis.com/css2?family=Oswald:wght@300;400;500;600;700&display=swap" rel="stylesheet">
<style>
  :root {
    --orange: #ef8560;
    --black: #000000;
    --ink: #222222;
    --ink-soft: #333333;
    --white: #ffffff;
    --field-text: #8a8a8a;
    --footer-bg: #232323;
    --active-tab: #c9653f;
  }
  * { box-sizing: border-box; margin: 0; padding: 0; }
  html, body { width: 1200px; height: 2400px; overflow: hidden; }
  body {
    position: relative;
    background: var(--white);
    font-family: "Oswald", "Arial Narrow", sans-serif;
    color: var(--ink);
  }
  .abs { position: absolute; }

  /* Hero */
  .hero { left: 0; top: 0; width: 1200px; height: 852px; background: var(--black); overflow: hidden; }
  .hero-photo {
    left: 0; top: 0; width: 1200px; height: 852px;
    background:
      radial-gradient(ellipse 420px 180px at 600px 130px, #1d2a3a 0%, rgba(0,0,0,0) 70%),
      radial-gradient(ellipse 520px 160px at 600px 780px, #1a222c 0%, rgba(0,0,0,0) 75%),
      #020305;
  }

  /* Navigation */
  .nav { left: 100px; top: 24px; width: 1000px; height: 40px; }
  .nav-left {
    left: 0; top: 0; width: 490px; height: 40px; background: var(--white);
    border-radius: 10px 0 0 10px;
  }
  .nav-right {
    left: 464px; top: 0; width: 536px; height: 40px; background: var(--orange);
    border-radius: 0 10px 10px 0;
  }
  .nav-link { top: 0; line-height: 40px; font-size: 11px; font-weight: 500; color: var(--ink); letter-spacing: 0.2px; }
  .nav-search { left: 387px; top: 11px; }
  .nav-tab { top: 0; font-size: 11px; font-weight: 500; color: var(--white); height: 40px; line-height: 40px; padding: 0 11px; }
  .nav-tab.is-active { background: var(--active-tab); }
  .brand-badge {
    left: 467px; top: -8px; width: 66px; height: 66px; border-radius: 50%;
    background: #1b1b1b; border: 3px solid var(--orange);
    display: flex; align-items: center; justify-content: center; text-align: center;
    font-size: 9px; font-weight: 600; color: var(--white); line-height: 1.1;
  }

  /* Hero copy */
  .hero-kicker { left: 0; top: 132px; width: 1200px; text-align: center; font-size: 56px; font-weight: 300; color: var(--orange); line-height: 1; }
  .hero-title { left: 0; top: 196px; width: 1200px; text-align: center; font-size: 56px; font-weight: 700; color: var(--white); letter-spacing: 0; line-height: 1; }
  .hero-sub { left: 0; top: 278px; width: 1200px; text-align: center; font-size: 25px; font-weight: 300; color: var(--white); line-height: 1.15; }
  .hero-swoosh { left: 288px; top: 286px; }

  /* Form */
  .field {
    background: var(--white); border-radius: 8px;
    font-size: 18px; font-weight: 300; color: var(--field-text);
    padding: 0 36px; line-height: 45px;
  }
  .field-message { line-height: 1; padding-top: 18px; }
  .btn-send {
    left: 522px; top: 758px; width: 154px; height: 46px; background: var(--orange);
    border-radius: 10px; color: var(--white); font-size: 25px; font-weight: 600;
    text-align: center; line-height: 46px;
  }

  /* Media */
  .media { border-radius: 22px; }
  .map { left: 98px; top: 894px; width: 455px; height: 545px; background: linear-gradient(150deg, #ece2c6 0%, #e8dcbc 45%, #9cc8c8 70%, #7eb8c0 100%); }
  .photo-vans { left: 576px; top: 894px; width: 523px; height: 290px; background: linear-gradient(180deg, #3c4b55 0%, #6d8590 55%, #38434b 100%); }
  .photo-dock-a { left: 576px; top: 1208px; width: 253px; height: 231px; background: linear-gradient(180deg, #b9b2a4 0%, #6f7a5a 55%, #c6c2b8 100%); }
  .photo-dock-b { left: 846px; top: 1208px; width: 253px; height: 231px; background: linear-gradient(180deg, #ddd8cc 0%, #b59a6b 50%, #c9ccd0 100%); }
  .media-label { top: 1455px; font-size: 32px; font-weight: 400; color: var(--ink); }

  /* Footer */
  .footer { left: 0; top: 1528px; width: 1200px; height: 294px; background: var(--footer-bg); color: var(--white); }
  .footer-badge {
    left: 102px; top: 94px; width: 62px; height: 62px; border-radius: 50%;
    background: var(--orange); display: flex; align-items: center; justify-content: center;
    text-align: center; font-size: 8px; font-weight: 600; line-height: 1.1; color: var(--white);
  }
  .footer-tagline { left: 102px; top: 178px; font-size: 13px; font-weight: 500; line-height: 1.1; }
  .footer-col h3 { font-size: 14px; font-weight: 500; margin-bottom: 10px; }
  .footer-col li { list-style: none; font-size: 9px; font-weight: 400; line-height: 23px; }
  .footer-note { font-size: 6.5px; line-height: 1.35; width: 150px; font-weight: 400; }
  .footer-phone { font-size: 24px; font-weight: 600; margin-top: 12px; letter-spacing: 0.5px; }
  .social { display: flex; gap: 7px; margin-top: 8px; }
  .social span { width: 15px; height: 15px; border-radius: 50%; background: var(--white); }

  .globe-band {
    left: 0; top: 1822px; width: 1200px; height: 204px;
    background: radial-gradient(ellipse 900px 260px at 600px 260px, #3f87c4 0%, #1d4f86 45%, #0b1e3a 100%);
  }
  .copyright { left: 0; top: 1924px; width: 1200px; text-align: center; font-size: 20px; font-weight: 600; color: var(--white); }

  .page-title { left: 0; top: 2126px; width: 1200px; text-align: center; font-size: 98px; font-weight: 500; color: var(--ink-soft); line-height: 1; }
</style>
</head>
<body>

<section class="hero abs">
  <div class="hero-photo abs" role="img" aria-label="Dark front view of a delivery truck at night"></div>

  <nav class="nav abs">
    <div class="nav-left abs">
      <span class="nav-link abs" style="left:25px;">REQUEST A QUOTE</span>
      <span class="nav-link abs" style="left:154px;">SIGNUP/LOGIN ◯</span>
      <span class="nav-link abs" style="left:288px;">GET START</span>
      <svg class="nav-search abs" width="18" height="18" viewBox="0 0 18 18" aria-label="Search"><circle cx="7.5" cy="7.5" r="5.5" fill="none" stroke="#222" stroke-width="2"/><line x1="11.5" y1="11.5" x2="16" y2="16" stroke="#222" stroke-width="2"/></svg>
    </div>
    <div class="nav-right abs"></div>
    <span class="nav-tab abs" style="left:578px;">HOME</span>
    <span class="nav-tab abs" style="left:646px;">SERVICES</span>
    <span class="nav-tab abs" style="left:728px;">INDUSTRIES</span>
    <span class="nav-tab is-active abs" style="left:820px;">ABOUT US</span>
    <span class="nav-tab abs" style="left:904px;">CONTACTUS</span>
    <div class="brand-badge abs">CORVANE<br>FREIGHT</div>
  </nav>

  <div class="hero-kicker abs">LET'S MOVE</div>
  <h1 class="hero-title abs">YOUR BUSINESS FORWARD</h1>
  <svg class="hero-swoosh abs" width="624" height="36" viewBox="0 0 624 36">
    <path d="M2 26 Q18 12 34 8" fill="none" stroke="#c9d3dc" stroke-width="1.5"/>
    <path d="M622 26 Q606 12 590 8" fill="none" stroke="#c9d3dc" stroke-width="1.5"/>
  </svg>
  <p class="hero-sub abs">LET'S DISCUSS YOUR LOGISTICS NEEDS AND HOW WE<br>CAN HELP YOUR BUSINESS THRIVE</p>

  <form>
    <div class="field abs" style="left:103px;top:404px;width:490px;height:45px;">FIRST NAME</div>
    <div class="field abs" style="left:611px;top:404px;width:489px;height:45px;">LAST NAME</div>
    <div class="field abs" style="left:103px;top:464px;width:490px;height:45px;">EMAIL ID</div>
    <div class="field abs" style="left:611px;top:464px;width:489px;height:45px;">PHONE NUMBER</div>
    <div class="field field-message abs" style="left:103px;top:527px;width:997px;height:205px;">MESSAGE</div>
    <div class="btn-send abs">SEND</div>
  </form>
</section>

<section>
  <div class="media map abs" role="img" aria-label="Illustrated city map with route and location pin"></div>
  <div class="media photo-vans abs" role="img" aria-label="Fleet of white delivery vans in a depot"></div>
  <div class="media photo-dock-a abs" role="img" aria-label="Yellow trucks at a warehouse loading dock"></div>
  <div class="media photo-dock-b abs" role="img" aria-label="Trailers parked at a distribution center"></div>
  <h2 class="media-label abs" style="left:98px;">LOCATION</h2>
  <h2 class="media-label abs" style="left:590px;">PICTURES</h2>
</section>

<footer class="footer abs">
  <div class="footer-badge abs">CORVANE<br>FREIGHT</div>
  <p class="footer-tagline abs">READY TO MOVE YOUR<br>FREIGHT?</p>

  <div class="footer-col abs" style="left:426px;top:94px;">
    <h3>QUICK LINKS</h3>
    <ul><li>HOME</li><li>SERVICE</li><li>INDUSTRIES</li><li>REQUEST QUOTE</li><li>CONTACT US</li></ul>
  </div>
  <div class="footer-col abs" style="left:698px;top:94px;">
    <h3>SERVICES</h3>
    <ul><li>FREIGHT BROKERAGE</li><li>TRUCKLOAD</li><li>WAREHOUSING</li><li>LAST MILE DELIVERY</li></ul>
  </div>
  <div class="footer-col abs" style="left:966px;top:94px;">
    <h3>CONTACT INFO</h3>
    <p class="footer-note">WE MOVE FREIGHT ACROSS THE COUNTRY WITH CARE. OUR TEAM IS READY TO HELP YOU PLAN EVERY LOAD, TRACK EVERY MILE AND DELIVER ON TIME, EVERY TIME YOU SHIP.</p>
    <p class="footer-phone">123-456-7890</p>
    <div class="social"><span></span><span></span><span></span></div>
  </div>
</footer>

<div class="globe-band abs" role="img" aria-label="Earth at night with cargo containers circling the globe"></div>
<p class="copyright abs">© 2026. AN INDEPENDENT AGENT OF HARLOW CREST LLC.</p>

<h2 class="page-title abs">CONTACT US</h2>

</body>
</html>
```